Business card design for new eCommerce site focusing on integrity and strong businsess tactics

We need a business card that will stand out and be memorable. Something with color that matches our company logo colors. Think high end version of Pactivo. There are 2 logos provided. The parent company is called Amber Ledge Partners and we are presenting a new and very exciting eCommerce site called BrightHarborTrade.example.

Target Market(s)

Our target markets are in the Activities, Food and Beverage, Health and Beauty

Industry/Entity Type

Marketing

Contact Information for Business Card

We have 4 members that need cards...I will provide all info to the winner of the design contest
Business Address is
4870 West 63rd Avenue, Suite C207
Phoenix AZ 85731

Font styles to use
Serif
Sans Serif

Colors

Designer to choose colors to be used in the design.

Requirements
Must have
• The card must be memorable...should be unique in design but must exude integrity and be playful .
• I have provided several colors or our parent company...please feel free to use which ever
Nice to have
• I will leave this up to you. Feel free to use other images of your choosing that wraps around our client.....Activities, Dining, Health, Beauty
Should not have
• just dont be boring

```html
<!DOCTYPE html>
<html lang="en">
<head>
<meta charset="utf-8">
<title>Amber Ledge Partners – Business Card</title>
<link href="https://fonts.googleapis.com/css2?family=Open+Sans:wght@400;600;700&display=swap" rel="stylesheet">
<style>
  :root {
    --backdrop: #3b322e;
    --card: #141516;
    --card-edge: #1d1f20;
    --green: #7cae3a;
    --blue: #2b8fd2;
    --ink: #ffffff;
    --muted: #a9abad;
    --rule: #e9e9e9;
  }
  * { box-sizing: border-box; margin: 0; padding: 0; }
  html, body { width: 1200px; height: 864px; overflow: hidden; }
  body {
    background: var(--backdrop);
    font-family: "Open Sans", Arial, sans-serif;
    display: flex;
    align-items: center;
    justify-content: center;
    gap: 40px;
  }
  .card {
    width: 560px;
    height: 320px;
    background: var(--card);
    border: 1px solid var(--card-edge);
    border-radius: 4px;
    box-shadow: 0 14px 30px rgba(0,0,0,.45);
    position: relative;
    overflow: hidden;
    flex: none;
  }

  /* Front */
  .card-front {
    display: flex;
    flex-direction: column;
    align-items: center;
    justify-content: center;
  }
  .brand-mark {
    display: flex;
    align-items: center;
    gap: 12px;
  }
  .brand-dot {
    width: 22px; height: 22px;
    border-radius: 50%;
    background: var(--green);
    flex: none;
  }
  .brand-name {
    color: var(--green);
    font-weight: 700;
    font-size: 34px;
    letter-spacing: -0.5px;
  }
  .front-web {
    margin-top: 34px;
    color: var(--muted);
    font-size: 15px;
    letter-spacing: 3px;
  }

  /* Back */
  .card-back {
    display: flex;
    align-items: center;
    padding: 0 24px 0 26px;
  }
  .site-block { width: 212px; flex: none; }
  .site-name {
    color: var(--blue);
    font-weight: 700;
    font-size: 16px;
    letter-spacing: -0.3px;
    white-space: nowrap;
  }
  .site-tagline {
    margin-top: 4px;
    color: var(--muted);
    font-size: 11px;
    letter-spacing: 0.3px;
    white-space: nowrap;
  }
  .divider {
    flex: none;
    width: 2px;
    height: 180px;
    margin: 0 18px 0 8px;
    background: linear-gradient(to bottom, rgba(233,233,233,0), var(--rule) 50%, rgba(233,233,233,0));
  }
  .contact-block {
    flex: 1;
    min-width: 0;
    color: var(--ink);
    font-size: 13px;
    line-height: 1.35;
    white-space: nowrap;
  }
  .person-name { color: var(--blue); font-weight: 700; font-size: 14px; }
  .person-title { color: var(--green); font-weight: 600; font-size: 14px; margin-bottom: 2px; }
  .contact-list { list-style: none; margin-top: 6px; }
  .contact-list li { display: flex; align-items: center; gap: 8px; }
  .contact-list svg { width: 11px; height: 11px; fill: var(--blue); flex: none; }
</style>
</head>
<body>
  <section class="card card-front">
    <div class="brand-mark">
      <span class="brand-dot"></span>
      <span class="brand-name">Amber Ledge Partners</span>
    </div>
    <p class="front-web">www.brightharbortrade.example</p>
  </section>

  <section class="card card-back">
    <div class="site-block">
      <p class="site-name">BrightHarborTrade.example</p>
      <p class="site-tagline">Activities-Dining-Health-Beauty</p>
    </div>
    <div class="divider"></div>
    <div class="contact-block">
      <p class="person-name">JORDAN RIVERA</p>
      <p class="person-title">CEO/FOUNDER</p>
      <p>4870 West 63rd Avenue</p>
      <p>Suite C207</p>
      <p>Phoenix AZ 85731</p>
      <ul class="contact-list">
        <li>
          <svg viewBox="0 0 12 12" aria-hidden="true"><path d="M2.5 1l2 2.3-1 1.2a7 7 0 0 0 4 4l1.2-1 2.3 2-1.2 1.5C5 11 1 7 1 2.2z"/></svg>
          555 014 2738
        </li>
        <li>
          <svg viewBox="0 0 12 12" aria-hidden="true"><path d="M3 0h6v12H3zM4 1.5v8h4v-8z" fill-rule="evenodd"/></svg>
          555 019 6482
        </li>
        <li>
          <svg viewBox="0 0 12 12" aria-hidden="true"><path d="M0 2h12v8H0zM1 3l5 3.5L11 3z" fill-rule="evenodd"/></svg>
          jordan@brightharbortrade.example
        </li>
        <li>
          <svg viewBox="0 0 12 12" aria-hidden="true"><circle cx="6" cy="6" r="6"/><path d="M1 6h10M6 0v12" stroke="#141516" stroke-width="1"/></svg>
          www.brightharbortrade.example
        </li>
      </ul>
    </div>
  </section>
</body>
</html>
```